Structural Engineering Business Card

Brookvane Drafting does residential house plans for clients in Central Florida. Would like simple but elegant business card that is appropriate for a house plan engineering company. Prefer black business card with black/white them but open to other shades of blue. I uploaded a sample card that I came across that looked good but please come up with your own creative designs.

Contact Information for Business Card

Name, Title, Phone, Email, Address, website

```html
<!DOCTYPE html>
<html lang="en">
<head>
<meta charset="utf-8">
<title>Brookvane Drafting – Business Card</title>
<link href="https://fonts.googleapis.com/css2?family=Abril+Fatface&family=Poppins:wght@400;700&display=swap" rel="stylesheet">
<style>
  :root{
    --stage:#969494;
    --ink:#000000;
    --paper:#ffffff;
    --shadow:rgba(0,0,0,.45);
  }
  *{margin:0;padding:0;box-sizing:border-box}
  html,body{width:1075px;height:1200px;overflow:hidden;background:var(--stage);font-family:"Poppins",sans-serif}
  .card{position:absolute;left:206px;width:663px;overflow:hidden;box-shadow:3px 3px 3px var(--shadow)}
  .card--front{top:187px;height:396px;background:var(--paper)}
  .card--back{top:637px;height:394px;background:var(--ink)}

  .brand{font-weight:700;letter-spacing:.5px;white-space:nowrap;line-height:1;display:flex;align-items:center;gap:10px}
  .brand__square{display:inline-block;background:currentColor}
  .card--front .brand{position:absolute;right:44px;top:84px;font-size:30px;color:var(--ink)}
  .card--front .brand__square{width:18px;height:18px}

  .person{position:absolute;left:35px;top:222px}
  .person__name{font-family:"Abril Fatface",serif;font-size:21px;letter-spacing:.6px;line-height:1;color:var(--ink)}
  .person__title{font-size:16px;line-height:1.2;margin-top:2px;color:var(--ink)}

  .info-band{position:absolute;left:0;right:0;top:279px;bottom:0;background:var(--ink);color:var(--paper)}
  .info-band__tab{position:absolute;left:35px;top:0;width:234px;height:6px;background:var(--paper)}
  .contacts{position:absolute;left:35px;top:22px;list-style:none;font-size:18px;line-height:23.5px}
  .contacts li{display:flex;align-items:center;gap:6px}
  .contacts svg{width:17px;height:17px;fill:var(--paper);flex:none}
  .address{position:absolute;right:41px;top:49px;text-align:right;font-size:18px;line-height:24px}

  .card--back .brand{position:absolute;left:0;right:0;top:166px;justify-content:center;font-size:46px;color:var(--paper)}
  .card--back .brand__square{width:28px;height:28px}
  .web-strip{position:absolute;left:0;right:0;bottom:0;height:44px;background:var(--paper);color:var(--ink);display:flex;align-items:center;justify-content:center;font-size:17px}
</style>
</head>
<body>

<section class="card card--front">
  <div class="brand"><span class="brand__square"></span>BROOKVANE DRAFTING</div>

  <div class="person">
    <div class="person__name">DANIEL MERCER</div>
    <div class="person__title">Managing Director</div>
  </div>

  <div class="info-band">
    <div class="info-band__tab"></div>
    <ul class="contacts">
      <li>
        <svg viewBox="0 0 24 24" aria-hidden="true"><path d="M6.6 10.8a15.1 15.1 0 0 0 6.6 6.6l2.2-2.2a1 1 0 0 1 1-.25 11.4 11.4 0 0 0 3.6.57 1 1 0 0 1 1 1V20a1 1 0 0 1-1 1A17 17 0 0 1 3 4a1 1 0 0 1 1-1h3.5a1 1 0 0 1 1 1c0 1.25.2 2.45.57 3.57a1 1 0 0 1-.25 1z"/></svg>
        044-555 018 274
      </li>
      <li>
        <svg viewBox="0 0 24 24" aria-hidden="true"><path d="M2 5h20v14H2z M3.5 6.5 12 13l8.5-6.5" fill="none" stroke="#fff" stroke-width="2"/></svg>
        info@brookvane.com
      </li>
      <li>
        <svg viewBox="0 0 24 24" aria-hidden="true"><g fill="none" stroke="#fff" stroke-width="1.8"><circle cx="12" cy="12" r="9.5"/><ellipse cx="12" cy="12" rx="4" ry="9.5"/><path d="M2.5 12h19M4 7h16M4 17h16"/></g></svg>
        www.brookvane.com
      </li>
    </ul>
    <div class="address">421, Address line goes here<br>45452,Country Name</div>
  </div>
</section>

<section class="card card--back">
  <div class="brand"><span class="brand__square"></span>BROOKVANE DRAFTING</div>
  <div class="web-strip">www.brookvane.com</div>
</section>

</body>
</html>
```